RW Holloway LLC Business Card - Civil Engineering & Consulting Firm

We need a Business Card that is elegant, and masculine.  It is our Professional Civil Engineering & Consulting Company located in San Antonio TX (Not s construction or builder firm- no gears & no tool images please). We provide civil engineering services including  commercial site plans, grading and drainage plans, utility plans, hydraulics and hydrology, land planning, utility coordination, and other general civil engineering services related to commercial and residential development.
We have 2 existing Logos. We would like to convey reliability, strength, trustworthiness and attention to detail.  Blues and orange tones as per logo We are OK with the use of a darker blue in the mix.  We have 2 logo versions - Full Company Name Logo to go on the back of card, & Small Icon Logo for the front w/ personal Info.

Target Market(s)
Architects, Real Estate Developers, Other Strctural Engineers, Surveyers, General Contractors
Industry/Entity Type
Professional Civil Engineering
Contact Information for Business Card
Name, Position, Address, Cell & Office #, email, and company website
Font styles to use
Other font styles liked:
- Avian
Requirements
Should not have
- No Tools, No Gears, no Cranes, or Construction Equipment.

```html
<!DOCTYPE html>
<html lang="en">
<head>
<meta charset="utf-8">
<title>RW Holloway LLC – Business Cards</title>
<link href="https://fonts.googleapis.com/css2?family=Arimo:ital,wght@0,400;0,700;1,400;1,700&display=swap" rel="stylesheet">
<style>
  :root {
    --page: #141416;
    --navy: #0d0d33;
    --navy-pattern: #1c1c58;
    --orange: #e8861f;
    --sky: #6aa6d6;
    --amber: #f2ac12;
    --ink: #ffffff;
  }
  * { box-sizing: border-box; margin: 0; padding: 0; }
  html, body { width: 747px; height: 1200px; overflow: hidden; }
  body {
    background: var(--page);
    font-family: "Arimo", Arial, sans-serif;
    color: var(--ink);
    display: flex;
    flex-direction: column;
    align-items: center;
    justify-content: space-evenly;
  }
  .card {
    position: relative;
    width: 640px;
    height: 366px;
    border-radius: 22px;
    background: var(--navy);
    border-bottom: 3px solid var(--orange);
    border-right: 2px solid var(--orange);
    overflow: hidden;
  }

  /* back */
  .card-back .pattern {
    position: absolute; inset: 0;
    background: linear-gradient(135deg, var(--navy-pattern), var(--navy) 70%);
  }
  .card-back .brand {
    position: absolute;
    left: 0; right: 0; top: 150px;
    text-align: center;
  }
  .brand-name {
    font-size: 44px;
    font-weight: 400;
    letter-spacing: 3px;
    color: var(--sky);
  }
  .brand-tag {
    margin-top: 10px;
    font-size: 11px;
    letter-spacing: 5px;
    text-transform: uppercase;
    color: var(--orange);
  }

  /* front */
  .card-front .mark {
    position: absolute;
    left: 44px; top: 158px;
    width: 230px;
    display: flex; align-items: center; gap: 10px;
  }
  .mark-square { width: 18px; height: 18px; background: var(--orange); flex: none; }
  .mark-name {
    font-size: 22px;
    font-weight: 700;
    color: var(--orange);
    line-height: 1;
    white-space: nowrap;
  }
  .mark-rule {
    position: absolute; left: 44px; top: 200px;
    width: 220px; height: 5px;
    background: linear-gradient(90deg, var(--sky) 0 55%, var(--orange) 55% 85%, var(--amber) 85%);
  }
  .details {
    position: absolute;
    left: 300px; top: 70px;
    font-size: 15px;
    line-height: 1.45;
  }
  .person-name { font-size: 22px; font-weight: 700; color: var(--orange); }
  .person-title { margin-bottom: 10px; }
  .address { margin-bottom: 8px; }
  .contact { list-style: none; }
  .contact li { display: flex; align-items: center; gap: 8px; }
  .contact svg { width: 13px; height: 13px; flex: none; }
</style>
</head>
<body>

<section class="card card-back">
  <div class="pattern" role="img" aria-label="Repeating tone-on-tone monogram pattern across the card back"></div>
  <div class="brand">
    <div class="brand-name">RW Holloway LLC</div>
    <div class="brand-tag">Consulting Engineers</div>
  </div>
</section>

<section class="card card-front">
  <div class="mark"><span class="mark-square"></span><span class="mark-name">RW Holloway LLC</span></div>
  <div class="mark-rule"></div>
  <div class="details">
    <div class="person-name">Robert W. Holloway, P.E.</div>
    <div class="person-title">Principal</div>
    <div class="address">4410 Ridgeline Way<br>Ridgeview, TX 78000</div>
    <ul class="contact">
      <li><svg viewBox="0 0 12 12"><rect x="3" y="0.5" width="6" height="11" rx="1" fill="none" stroke="var(--orange)" stroke-width="1.3"/></svg>210.555.0147</li>
      <li><svg viewBox="0 0 12 12"><path d="M2 1l3 .5 .5 2.5-1.5 1a7 7 0 0 0 3 3l1-1.5 2.5.5.5 3C6 11 1 6 2 1z" fill="var(--orange)"/></svg>210.555.0190</li>
      <li><svg viewBox="0 0 12 12"><rect x="0.7" y="2.5" width="10.6" height="7" fill="none" stroke="var(--orange)" stroke-width="1.2"/><path d="M1 3l5 4 5-4" fill="none" stroke="var(--orange)" stroke-width="1.2"/></svg>robert.holloway@rw-holloway.com</li>
      <li><svg viewBox="0 0 12 12"><circle cx="6" cy="6" r="5" fill="none" stroke="var(--orange)" stroke-width="1.2"/><path d="M1 6h10M6 1c-3 3-3 7 0 10M6 1c3 3 3 7 0 10" fill="none" stroke="var(--orange)" stroke-width="1"/></svg>www.rw-holloway.com</li>
      <li><svg viewBox="0 0 12 12"><rect x="1" y="1" width="10" height="10" rx="1.5" fill="var(--orange)"/></svg>rw-holloway-llc</li>
    </ul>
  </div>
</section>

<section class="card card-front">
  <div class="mark"><span class="mark-square"></span><span class="mark-name">RW Holloway LLC</span></div>
  <div class="mark-rule"></div>
  <div class="details">
    <div class="person-name">Dana Whitfield</div>
    <div class="person-title">Principal</div>
    <div class="address">4410 Ridgeline Way<br>Ridgeview, TX 78000</div>
    <ul class="contact">
      <li><svg viewBox="0 0 12 12"><rect x="3" y="0.5" width="6" height="11" rx="1" fill="none" stroke="var(--orange)" stroke-width="1.3"/></svg>469.555.0128</li>
      <li><svg viewBox="0 0 12 12"><path d="M2 1l3 .5 .5 2.5-1.5 1a7 7 0 0 0 3 3l1-1.5 2.5.5.5 3C6 11 1 6 2 1z" fill="var(--orange)"/></svg>210.555.0190</li>
      <li><svg viewBox="0 0 12 12"><rect x="0.7" y="2.5" width="10.6" height="7" fill="none" stroke="var(--orange)" stroke-width="1.2"/><path d="M1 3l5 4 5-4" fill="none" stroke="var(--orange)" stroke-width="1.2"/></svg>dana.whitfield@rw-holloway.com</li>
      <li><svg viewBox="0 0 12 12"><circle cx="6" cy="6" r="5" fill="none" stroke="var(--orange)" stroke-width="1.2"/><path d="M1 6h10M6 1c-3 3-3 7 0 10M6 1c3 3 3 7 0 10" fill="none" stroke="var(--orange)" stroke-width="1"/></svg>www.rw-holloway.com</li>
      <li><svg viewBox="0 0 12 12"><rect x="1" y="1" width="10" height="10" rx="1.5" fill="var(--orange)"/></svg>rw-holloway-llc</li>
    </ul>
  </div>
</section>

</body>
</html>
```